Ledgerwise Forge - WordPress Theme & Logo

Design a logo and Wordpress website design for Ledgerwise Forge. Ledgerwise Forge provides cryptocurrency development services to clients who need a team to create & continue developing a new cryptocurrency or who want to replace their current cryptocurrency development team. more details in the attached document.
Updates

Target Market(s)

Entrepreneurs who are building a business / platform that makes use of an underlying cryptocurrency.

Logo Text

LF or Ledgerwise Forge

Coding

Coded - Design and coding required

Font styles to use
Sans Serif

Requirements
Must have
• Professional logo, complete coded Wordpress theme for all pages, containing all specified links and buttons
Nice to have
• It would be nice if the buttons that are meant to integrate with Dealtrail contain the necessary code for that. I can provide any necessary Dealtrail details from my account.
Should not have
• Slow loading time

```html
<!DOCTYPE html>
<html lang="en">
<head>
<meta charset="utf-8">
<title>Ledgerwise Forge – Cryptocurrency Development</title>
<link rel="stylesheet" href="https://fonts.googleapis.com/css2?family=Poppins:wght@300;400;600;700&family=Roboto:wght@400;500;700&display=swap">
<style>
:root{
  --purple:#7d2595;
  --blue:#1b79cc;
  --grad:linear-gradient(90deg,#86218f 0%,#1b79cc 100%);
  --ink:#111418;
  --body:#5c5f66;
  --muted:#7a7d84;
  --light:#f3f3f4;
  --white:#fff;
}
*{box-sizing:border-box;margin:0;padding:0}
html,body{width:1200px;height:3446px;overflow:hidden}
body{position:relative;font-family:'Roboto',sans-serif;color:var(--body);background:var(--white)}
.abs{position:absolute}
.btn{position:absolute;display:flex;align-items:center;justify-content:center;gap:8px;background:var(--grad);color:#fff;font:500 15px 'Roboto',sans-serif;border-radius:22px;text-decoration:none}
.btn .arrow{width:14px;height:14px;border-radius:50%;background:#fff;display:inline-flex;align-items:center;justify-content:center}
.btn .arrow::after{content:"";border:solid var(--purple);border-width:0 2px 2px 0;width:4px;height:4px;transform:rotate(-45deg);margin-left:-2px}
.section-title{position:absolute;left:0;width:1200px;text-align:center;font:300 38px 'Poppins',sans-serif;color:var(--ink)}
.section-title b{font-weight:700}

/* header */
.site-header{position:absolute;top:0;left:0;width:1200px;height:98px;background:#fff}
.brand{position:absolute;left:68px;top:30px;display:flex;align-items:center;gap:12px;font:600 21px 'Poppins',sans-serif;color:#1d1f24}
.brand .dot{width:30px;height:30px;border-radius:50%;background:var(--purple)}
.nav{position:absolute;top:39px;left:344px;display:flex;gap:23px;font:500 15px 'Roboto',sans-serif;color:#1d1f24}
.nav .active{color:var(--blue)}
.header-cta{left:891px;top:30px;width:241px;height:38px}

/* hero */
.hero{position:absolute;top:98px;left:0;width:1200px;height:608px;background:radial-gradient(circle at 80% 40%,#b98a4e 0%,#5a4030 28%,#243049 60%,#151c2e 100%)}
.hero h1{position:absolute;left:110px;top:128px;font:400 38px/46px 'Poppins',sans-serif;color:#fff}
.hero h1 b{font-weight:700}
.hero p{position:absolute;left:110px;top:292px;width:560px;font:500 15px/27.5px 'Roboto',sans-serif;color:#fff}
.hero .btn{left:110px;top:432px;width:258px;height:40px}

/* why */
.why{position:absolute;top:706px;left:0;width:1200px;height:558px;background:#fff}
.hex{position:absolute;top:179px;width:250px;height:290px;filter:drop-shadow(0 8px 14px rgba(0,0,0,.12))}
.hex .body{position:absolute;top:38px;left:0;width:250px;height:252px;background:#fff;clip-path:polygon(50% 0,100% 18%,100% 74%,50% 100%,0 74%,0 18%)}
.hex .cap{position:absolute;top:0;left:44px;width:162px;height:96px;background:var(--grad);clip-path:polygon(50% 0,100% 50%,50% 100%,0 50%)}
.hex h3{position:absolute;top:126px;width:250px;text-align:center;font:500 19px 'Roboto',sans-serif;color:var(--ink)}
.hex p{position:absolute;top:164px;left:10px;width:230px;text-align:center;font:400 14px/24px 'Roboto',sans-serif;color:var(--body)}

/* who */
.who{position:absolute;top:1264px;left:0;width:1200px;height:392px;background:var(--light)}
.who .photo{position:absolute;left:0;top:0;width:589px;height:392px;background:linear-gradient(135deg,#2b4a63 0%,#3d7fa3 45%,#1c2c3f 100%)}
.who h2{position:absolute;left:643px;top:54px;font:300 38px 'Poppins',sans-serif;color:var(--ink)}
.who h2 b{font-weight:700}
.who p{position:absolute;left:643px;top:122px;width:450px;font:400 14px/26.6px 'Roboto',sans-serif;color:var(--body)}
.who .btn{left:643px;top:283px;width:166px;height:45px}

/* clients */
.client{position:absolute;top:1836px;width:310px}
.client .card{position:absolute;top:44px;left:0;width:310px;height:188px;background:#fff;border-radius:10px;box-shadow:0 6px 16px rgba(0,0,0,.1);border-top:2px solid transparent;background-image:linear-gradient(#fff,#fff),var(--grad);background-origin:border-box;background-clip:padding-box,border-box}
.client .avatar{position:absolute;left:110px;top:0;width:90px;height:90px;border-radius:50%;background:linear-gradient(160deg,#c9ccd2,#7c828c);border:3px solid #fff;box-shadow:0 0 0 1px #ddd}
.client p{position:absolute;top:118px;left:20px;width:270px;text-align:center;font:400 14px/25.5px 'Roboto',sans-serif;color:var(--body)}
.client .name{position:absolute;top:256px;width:310px;text-align:center;font:500 15px 'Roboto',sans-serif;color:var(--ink)}
.client .name small{font-size:10px;font-weight:400}
.client .stars{position:absolute;top:278px;width:310px;text-align:center;color:#f2c200;font-size:13px;letter-spacing:1px}

/* services */
.services{position:absolute;top:2241px;left:0;width:1200px;height:825px;background:var(--light)}
.services .intro{position:absolute;left:120px;width:960px;text-align:center;font:400 14px/24px 'Roboto',sans-serif;color:var(--body)}
.svc{position:absolute;top:277px;width:313px;height:354px;background:#fff;border-radius:10px;box-shadow:0 6px 16px rgba(0,0,0,.08)}
.svc .art{position:absolute;left:91px;top:20px;width:130px;height:110px;border-radius:8px;background:linear-gradient(135deg,#c7d8f2,#8f7fd6 60%,#3f8fd8)}
.svc h3{position:absolute;top:153px;width:313px;text-align:center;font:500 16px 'Roboto',sans-serif;color:var(--ink)}
.svc p{position:absolute;top:194px;left:16px;width:281px;text-align:center;font:400 14px/25px 'Roboto',sans-serif;color:var(--muted)}
.chev{position:absolute;top:437px;width:22px;height:22px;border:solid #b5b7bb;border-width:0 3px 3px 0}
.services .btn{left:471px;top:688px;width:258px;height:40px}

/* footer */
.site-footer{position:absolute;top:3066px;left:0;width:1200px;height:380px;background:linear-gradient(100deg,#7a2598 0%,#4f3fb0 50%,#1477c8 100%);color:#fff}
.site-footer h4{position:absolute;top:83px;font:500 18px 'Roboto',sans-serif}
.contact-list{position:absolute;left:110px;top:128px;list-style:none;font:400 14px/20px 'Roboto',sans-serif}
.contact-list li{display:flex;gap:12px;margin-bottom:13px}
.contact-list svg{flex:none;margin-top:3px}
.links{position:absolute;top:130px;list-style:none;font:400 14px/26.6px 'Roboto',sans-serif}
.subscribe .field{position:absolute;left:715px;top:127px;width:236px;height:44px;border-radius:22px;background:#fff;color:#8a8a8a;font:400 11px 'Roboto',sans-serif;padding:16px 22px}
.subscribe .submit{position:absolute;left:965px;top:127px;width:122px;height:44px;border-radius:22px;background:#7d2595;font:700 16px 'Roboto',sans-serif;display:flex;align-items:center;justify-content:center}
.subscribe .consent{position:absolute;left:711px;top:195px;font:500 13px 'Roboto',sans-serif;display:flex;gap:8px;align-items:center}
.social{position:absolute;left:711px;top:230px;display:flex;gap:10px}
.social span{width:32px;height:32px;border-radius:50%;border:1.5px solid #fff}
.copyright{position:absolute;top:330px;width:1200px;text-align:center;font:400 13px 'Roboto',sans-serif}
</style>
</head>
<body>

<header class="site-header">
  <div class="brand"><span class="dot"></span>Ledgerwise Forge</div>
  <nav class="nav">
    <span class="active">Home</span><span>About Us</span><span>Our Services</span><span>Service Tiers</span><span>Testimonials</span><span>Blog</span>
  </nav>
  <a class="btn header-cta">Schedule a Free Consultation</a>
</header>

<section class="hero" role="img" aria-label="Glowing gold cryptocurrency coin over a dark network of binary code">
  <h1><b>Your own cryptocurrency.</b><br><b>Secure,</b> easy to use, &amp; built<br>by an expert team.</h1>
  <p>Ledgerwise Forge adds professionalism to cryptocurrency development. Our done-for-you service covers everything from development and IT operations to ongoing support. You have access to a full team, for less than the typical cost of a single developer.</p>
  <a class="btn">Schedule a Free Consultation <span class="arrow"></span></a>
</section>

<section class="why">
  <h2 class="section-title" style="top:78px"><b>Why choose</b> Ledgerwise Forge</h2>
  <div class="hex" style="left:175px"><div class="body"></div><div class="cap"></div><h3>Value</h3><p>A team of experts, regular updates, and fixed costs</p></div>
  <div class="hex" style="left:475px"><div class="body"></div><div class="cap"></div><h3>Support</h3><p>Receive advice and other services, beyond development.</p></div>
  <div class="hex" style="left:774px"><div class="body"></div><div class="cap"></div><h3>Commitment</h3><p>Enjoy regular updates and new features.</p></div>
</section>

<section class="who">
  <div class="photo" role="img" aria-label="Aerial city at night overlaid with glowing coin symbols"></div>
  <h2><b>Who</b> We Are</h2>
  <p>In addition to creating and enhancing cryptocurrencies for clients, the Ledgerwise Forge team has been running the Corvane cryptocurrency since 2017. We prefer long-term relationships, enabling us to deliver the very highest quality and giving you peace of mind that you've got aprofessional and trustworthy team at your side.</p>
  <a class="btn">READ MORE <span class="arrow"></span></a>
</section>

<h2 class="section-title" style="top:1750px"><b>What Our</b> Clients Say</h2>
<div class="client" style="left:111px"><div class="card"></div><div class="avatar" role="img" aria-label="Client portrait"></div><p>Sed ut perspiciatis unde omnis iste natus error sit voluptatem accusantium doloremque laudantium, totam rem aperiam, eaque ipsa</p><div class="name">Dana Whitlock, <small>Chairman NKV</small></div><div class="stars">★★★★★</div></div>
<div class="client" style="left:445px"><div class="card"></div><div class="avatar" role="img" aria-label="Client portrait"></div><p>Sed ut perspiciatis unde omnis iste natus error sit voluptatem accusantium doloremque laudantium, totam rem aperiam, eaque ipsa</p><div class="name">Mei Laurent, <small>Project Manager</small></div><div class="stars">★★★★★</div></div>
<div class="client" style="left:779px"><div class="card"></div><div class="avatar" role="img" aria-label="Client portrait"></div><p>Sed ut perspiciatis unde omnis iste natus error sit voluptatem accusantium doloremque laudantium, totam rem aperiam, eaque ipsa</p><div class="name">Owen Pratt, <small>Chairman NKV</small></div><div class="stars">★★★★★</div></div>

<section class="services">
  <h2 class="section-title" style="top:52px"><b>Our</b> Services</h2>
  <p class="intro" style="top:120px">Ledgerwise Forge provides a complete service that handles the development, IT operations and support for your cryptocurrency. Cryptocurrency development can be difficult and complex, and a quality development team is hard to find and expensive. expensive.</p>
  <p class="intro" style="top:182px">Ledgerwise Forge has an experienced team that has helped several clients launch and enhance their cryptocurrencies, including successfully running the Corvane cryptocurrency since 2017, and writing a next-generation cryptocurrency from scratch.</p>
  <div class="chev" style="left:42px;transform:rotate(135deg)"></div>
  <div class="svc" style="left:107px"><div class="art" role="img" aria-label="Isometric illustration of connected blockchain nodes"></div><h3>Blockchain Creation &amp; Launch</h3><p>Base fixed price for cryptocurrency development &amp; launch–would be customizable based on client requirements</p></div>
  <div class="svc" style="left:444px"><div class="art" role="img" aria-label="Isometric illustration of a server platform"></div><h3>Basic offering</h3><p>Lower cost per month<br>Slower release schedule<br>Client assists with testing new releases<br>Less input into future roadmap/features<br>Limited support hours/priority available</p></div>
  <div class="svc" style="left:781px"><div class="art" role="img" aria-label="Isometric illustration of coins and cubes network"></div><h3>Full service offering</h3><p>Mid-range cost per month<br>Releases every 1.5 - 2 months<br>Client can help request/prioritize new<br>Full testing by my team prior to release<br>Priority support during normal business</p></div>
  <div class="chev" style="left:1134px;transform:rotate(-45deg)"></div>
  <a class="btn">Schedule a Free Consultation <span class="arrow"></span></a>
</section>

<footer class="site-footer">
  <h4 style="left:110px">Contact Us</h4>
  <ul class="contact-list">
    <li><svg width="12" height="15" viewBox="0 0 12 15"><path d="M6 0a6 6 0 0 0-6 6c0 4.5 6 9 6 9s6-4.5 6-9a6 6 0 0 0-6-6zm0 8.5A2.5 2.5 0 1 1 6 3.5a2.5 2.5 0 0 1 0 5z" fill="#4aa3f0"/></svg><span>3501 Lorem ipsum dolor sit<br>amet, consectetur</span></li>
    <li><svg width="14" height="11" viewBox="0 0 14 11"><rect width="14" height="11" rx="1.5" fill="#4aa3f0"/><path d="M1 1.5l6 4.5 6-4.5" stroke="#fff" fill="none"/></svg><span>info@ledgerwiseforge.example</span></li>
    <li><svg width="13" height="13" viewBox="0 0 13 13"><path d="M3 0l2 3-1.5 1.5a8 8 0 0 0 5 5L10 8l3 2-1.5 3C5 12.5.5 8 0 1.5z" fill="#4aa3f0"/></svg><span>555.204.7100</span></li>
    <li><svg width="14" height="12" viewBox="0 0 14 12"><rect y="3" width="14" height="9" rx="1.5" fill="#4aa3f0"/><rect x="3" width="8" height="4" fill="#4aa3f0"/></svg><span>(555)&nbsp; 555 - 0199</span></li>
  </ul>
  <h4 style="left:395px">Links</h4>
  <ul class="links" style="left:395px"><li>Home</li><li>About Us</li><li>Our Services</li><li>Service Tiers</li><li>Testimonials</li></ul>
  <ul class="links" style="left:521px"><li>Terms &amp; Condition</li><li>Privacy Policy</li><li>Updates</li><li>Support</li><li>Contact</li></ul>
  <div class="subscribe">
    <h4 style="left:711px">Subscribe for Updates</h4>
    <div class="field">Emaill Address</div>
    <div class="submit">SUBMIT</div>
    <div class="consent"><svg width="12" height="12" viewBox="0 0 12 12"><rect x=".75" y=".75" width="10.5" height="10.5" rx="2" fill="none" stroke="#fff" stroke-width="1.5"/><path d="M3 6l2 2 4-4" stroke="#fff" stroke-width="1.5" fill="none"/></svg>Yes, Please Contact me.</div>
    <div class="social" aria-label="Social profiles"><span></span><span></span><span></span></div>
  </div>
  <div class="copyright">© 2021&nbsp; Ledgerwise Forge&nbsp; |&nbsp; All Rights Reserved</div>
</footer>

</body>
</html>
```